Coffee House With Cycling Theme Wants Business Cards

We want to create a business card for a coffee house that has a cycling theme. We expect to use the current logo on one side of the business card and we have been considering adding the words 'COFFEE HOUSE' underneath (see example). For the other side of the business card we want an interesting design with tag-line, address and social media links (the normal business card stuff). See examples provided but we are not fixed on having it exactly as shown, we are very open to great creative ideas. Please note our logo has the initials ‘KR' in orange embedded in the design and this must be retained. However, you can play with the words COFFEE HOUSE as well as use the orange color on the backside of the business card, as you see fit. For an image on the backside of the business card it can be a photo, hand-drawn or whatever but it must visually combine coffee and cycling in some way. The interior of the Coffee House will be reclaimed wood, rustic and have an urban feel to it with cycling artifacts hanging from the walls/ceiling, etc. Finally, it would be beneficial if the business card design elements can be easily used on flyers and other promotional assets. Good luck, we are looking forward to seeing your creative ideas.

Target Market(s)

Coffee lovers and cycling fans

Contact Information for Business Card

See project description.

Colors

Designer to choose colors to be used in the design.

Requirements
Must have
• Must use the current logo provided and combine a coffee and bike theme.
Nice to have
• Orange is used in current logo and could be used as an accent color on the backside of the business card.

```html
<!DOCTYPE html>
<html lang="en">
<head>
<meta charset="utf-8">
<title>KR Coffee House – Business Cards</title>
<link rel="stylesheet" href="https://fonts.googleapis.com/css2?family=Open+Sans:wght@400;600&family=Work+Sans:wght@400;500&display=swap">
<style>
  :root {
    --bg: #161616;
    --card: #262626;
    --card-edge: #1f1f1f;
    --orange: #f26a2a;
    --white: #f4f4f4;
    --muted: #d8d8d8;
  }
  * { box-sizing: border-box; margin: 0; padding: 0; }
  html, body { width: 1200px; height: 900px; overflow: hidden; background: var(--bg); }
  .stage {
    width: 1200px; height: 900px;
    display: flex; flex-direction: column; align-items: center; justify-content: center; gap: 40px;
  }
  .card {
    position: relative; width: 700px; height: 400px;
    background: linear-gradient(135deg, var(--card) 0%, #2d2d2d 60%, var(--card-edge) 100%);
    box-shadow: 0 10px 30px rgba(0,0,0,.6);
    overflow: hidden;
  }
  .brand-name {
    font-family: "Open Sans", sans-serif; font-weight: 600;
    color: var(--orange); line-height: 1;
  }
  .brand-mark {
    display: flex; align-items: center; gap: 18px;
  }
  .brand-dot {
    width: 26px; height: 26px; border-radius: 50%; background: var(--white);
  }

  /* front */
  .card--front { display: flex; flex-direction: column; align-items: center; }
  .card--front .brand-mark { margin-top: 80px; }
  .card--front .brand-initials { font-size: 110px; letter-spacing: 6px; }
  .card--front .brand-words { font-size: 50px; letter-spacing: 3px; margin-top: 10px; }
  .card--front .site {
    position: absolute; bottom: 36px; left: 0; right: 0; text-align: center;
    font-family: "Work Sans", sans-serif; font-size: 17px; color: var(--white); letter-spacing: .5px;
  }

  /* back */
  .card--back .logo-block {
    position: absolute; left: 40px; top: 70px; width: 300px;
    display: flex; flex-direction: column; align-items: center;
  }
  .card--back .brand-initials { font-size: 100px; letter-spacing: 5px; }
  .card--back .brand-words { font-size: 44px; letter-spacing: 2px; margin-top: 10px; white-space: nowrap; }
  .divider {
    position: absolute; left: 372px; top: 70px; width: 2px; height: 200px; background: var(--white);
  }
  .contact {
    position: absolute; left: 400px; top: 78px; right: 20px;
    font-family: "Work Sans", sans-serif; color: var(--white);
  }
  .contact__name {
    font-family: "Work Sans", sans-serif; font-weight: 500; color: var(--orange);
    font-size: 24px; letter-spacing: 1.5px; text-transform: uppercase;
  }
  .contact__role { font-size: 16px; margin-top: 2px; color: var(--muted); }
  .contact__address { font-size: 17px; line-height: 1.45; margin-top: 18px; }
  .contact__list { list-style: none; margin-top: 12px; font-size: 17px; line-height: 1.5; }
  .contact__list li { display: flex; align-items: center; gap: 10px; }
  .contact__list svg { width: 12px; height: 12px; flex: none; }

  .social-band {
    position: absolute; left: 0; right: 0; bottom: 46px; height: 38px;
    background: var(--orange);
    display: flex; align-items: center; padding-left: 180px; gap: 46px;
    font-family: "Work Sans", sans-serif; font-size: 18px; color: var(--white);
  }
  .social-band__item { display: flex; align-items: center; gap: 10px; }
  .social-band__dot { width: 18px; height: 18px; border-radius: 50%; background: var(--white); }
</style>
</head>
<body>
<main class="stage">

  <section class="card card--front" aria-label="Business card front">
    <div class="brand-mark">
      <span class="brand-name brand-initials">KR</span>
      <span class="brand-dot"></span>
    </div>
    <div class="brand-name brand-words">COFFEE HOUSE</div>
    <p class="site">www.krcoffeehouse.com</p>
  </section>

  <section class="card card--back" aria-label="Business card back">
    <div class="logo-block">
      <div class="brand-mark">
        <span class="brand-name brand-initials">KR</span>
        <span class="brand-dot"></span>
      </div>
      <div class="brand-name brand-words">COFFEE HOUSE</div>
    </div>

    <div class="divider"></div>

    <div class="contact">
      <h1 class="contact__name">Daniel Brooks</h1>
      <p class="contact__role">Director</p>
      <p class="contact__address">48b Harlow Street,<br>Westbury, NZ, 8024</p>
      <ul class="contact__list">
        <li>
          <svg viewBox="0 0 12 12" aria-hidden="true"><path d="M3 1 L5 3.5 L4 5 Q5 7 7 8 L8.5 7 L11 9 L9.5 11 Q5 10.5 1 3 Z" fill="none" stroke="#f26a2a" stroke-width="1.2"/></svg>
          (555) 014-2270
        </li>
        <li>
          <svg viewBox="0 0 12 12" aria-hidden="true"><rect x="1" y="2.5" width="10" height="7" fill="none" stroke="#f26a2a" stroke-width="1.2"/><path d="M1 2.5 L6 6.5 L11 2.5" fill="none" stroke="#f26a2a" stroke-width="1.2"/></svg>
          info@krcoffeehouse.com
        </li>
        <li>
          <svg viewBox="0 0 12 12" aria-hidden="true"><circle cx="6" cy="6" r="5" fill="none" stroke="#f26a2a" stroke-width="1.2"/><ellipse cx="6" cy="6" rx="2.2" ry="5" fill="none" stroke="#f26a2a" stroke-width="1"/><path d="M1 6 H11" stroke="#f26a2a" stroke-width="1"/></svg>
          www.krcoffeehouse.com
        </li>
      </ul>
    </div>

    <div class="social-band">
      <span class="social-band__item"><span class="social-band__dot"></span>krcoffeehouse.com</span>
      <span class="social-band__item"><span class="social-band__dot"></span>krcoffeehouse.com</span>
    </div>
  </section>

</main>
</body>
</html>
```